Business cards for a fun web development agency

Hi,I am building a web development agency. You can read about it on the website http://kite-loft.examplehost.com. Basically, I want to focus on free and open source products and stay as far away from the corporate business feeling as possible. I want to build a community so I want the business card to feel fun and approachable (at the risk of professional if need be). I am uploading some of my image assets in various file formats. Feel free to use them or make your own if you want just keeping in theme with the website.
Industry/Entity Type
Building
Contact Information for Business Card
Company Name: Boat ShedWebsite: www.kiteloftdev.example (it's currently in alpha on http://kite-loft.examplehost.com if you want to see the them we are trying to capture)My name is: Banner B. SchaferMy email: banner@boatsheddev.comMy phone: 0431 587 904
Look and feel

```html
<!DOCTYPE html>
<html lang="en">
<head>
<meta charset="utf-8">
<title>Kite Loft – Business Card</title>
<link rel="stylesheet" href="https://fonts.googleapis.com/css2?family=Exo+2:wght@500;600&family=Oxygen:wght@400&display=swap">
<style>
  :root {
    --page-bg: #e6e7e9;
    --card-top: #ffffff;
    --card-bottom: #e9eaec;
    --brand-blue: #1a8fc0;
    --deep-blue: #0f7fb0;
    --swoosh-grey: #9a9ca0;
    --ink: #3a3d42;
    --icon: #4d6f86;
  }
  * { margin: 0; padding: 0; box-sizing: border-box; }
  html, body { width: 1200px; height: 900px; overflow: hidden; }
  body {
    background: var(--page-bg);
    display: flex; align-items: center; justify-content: center;
  }
  .card {
    position: relative;
    width: 1000px; height: 570px;
    border-radius: 64px;
    overflow: hidden;
    background: linear-gradient(160deg, var(--card-top) 0%, #f4f4f5 55%, var(--card-bottom) 100%);
    box-shadow: 0 10px 30px rgba(0,0,0,.15);
  }
  .card__swoosh { position: absolute; inset: 0; width: 100%; height: 100%; }
  .contact-list {
    position: absolute; left: 42px; top: 128px;
    list-style: none;
    font-family: "Oxygen", sans-serif;
    font-size: 21px; letter-spacing: .5px; color: var(--ink);
  }
  .contact-list li { display: flex; align-items: center; height: 38px; }
  .contact-list svg { width: 22px; height: 22px; margin-right: 14px; fill: var(--icon); flex: none; }
  .contact-list .contact--small { font-size: 19px; }
  .brand {
    position: absolute; left: 400px; top: 178px;
    display: flex; align-items: center; gap: 18px;
    font-family: "Exo 2", sans-serif; font-weight: 600;
    font-size: 84px; letter-spacing: 2px;
    color: var(--brand-blue);
  }
  .brand__dot { width: 26px; height: 26px; border-radius: 50%; background: var(--brand-blue); }
  .holder {
    position: absolute; right: 120px; top: 318px;
    text-align: right; font-family: "Exo 2", sans-serif;
  }
  .holder__name { font-size: 31px; font-weight: 500; letter-spacing: 2px; color: var(--brand-blue); text-transform: uppercase; }
  .holder__role { margin-top: 4px; font-size: 19px; font-weight: 500; letter-spacing: 2px; color: var(--ink); text-transform: uppercase; }
</style>
</head>
<body>
  <div class="card">
    <svg class="card__swoosh" viewBox="0 0 1000 570" preserveAspectRatio="none" aria-hidden="true">
      <path d="M0 325 C300 445 700 480 1000 380 L1000 400 C700 500 300 465 0 345 Z" fill="var(--swoosh-grey)"/>
      <path d="M0 360 C300 495 700 515 1000 410 L1000 570 L0 570 Z" fill="var(--brand-blue)"/>
      <path d="M0 435 C300 545 700 560 1000 462 L1000 570 L0 570 Z" fill="var(--deep-blue)"/>
      <path d="M0 435 C300 545 700 560 1000 462" fill="none" stroke="#ffffff" stroke-width="7"/>
    </svg>

    <ul class="contact-list">
      <li><svg viewBox="0 0 24 24"><path d="M6.6 10.8a15.5 15.5 0 0 0 6.6 6.6l2.2-2.2c.3-.3.7-.4 1-.2 1.1.4 2.3.6 3.6.6.6 0 1 .4 1 1V20c0 .6-.4 1-1 1A17 17 0 0 1 3 4c0-.6.4-1 1-1h3.5c.6 0 1 .4 1 1 0 1.3.2 2.5.6 3.6.1.3 0 .7-.2 1z"/></svg>0431 587 904</li>
      <li><svg viewBox="0 0 24 24"><path d="M7 1h10a2 2 0 0 1 2 2v18a2 2 0 0 1-2 2H7a2 2 0 0 1-2-2V3a2 2 0 0 1 2-2zm0 3v14h10V4zm5 15.5a1 1 0 1 0 0 2 1 1 0 0 0 0-2z"/></svg>0431 587 904</li>
      <li><svg viewBox="0 0 24 24"><path d="M7 2h9v5H7zM3 8h18v13H3zm3 3v2h3v-2zm5 0v2h3v-2zm5 0v2h2v-2zM6 15v2h3v-2zm5 0v2h3v-2zm5 0v2h2v-2z"/></svg>0431 587 904</li>
      <li class="contact--small"><svg viewBox="0 0 24 24"><path d="M2 5h20v14H2zm2 2v.5l8 5 8-5V7zm0 2.8V17h16V9.8l-8 5z"/></svg>corwin@kiteloftdev.example</li>
      <li class="contact--small"><svg viewBox="0 0 24 24"><path d="M12 2a10 10 0 1 0 0 20 10 10 0 0 0 0-20zm6.9 6h-3a15 15 0 0 0-1.3-3.9A8 8 0 0 1 18.9 8zM12 4c.9 1.2 1.6 2.6 2 4h-4c.4-1.4 1.1-2.8 2-4zM4.3 14a8 8 0 0 1 0-4h3.4a16 16 0 0 0 0 4zm.8 2h3a15 15 0 0 0 1.3 3.9A8 8 0 0 1 5.1 16zM8 8H5.1a8 8 0 0 1 4.3-3.9C8.8 5.3 8.4 6.6 8 8zm4 12c-.9-1.2-1.6-2.6-2-4h4c-.4 1.4-1.1 2.8-2 4zm2.3-6H9.7a14 14 0 0 1 0-4h4.6a14 14 0 0 1 0 4zm.3 5.9c.6-1.2 1-2.5 1.3-3.9h3a8 8 0 0 1-4.3 3.9zm1.7-5.9a16 16 0 0 0 0-4h3.4a8 8 0 0 1 0 4z"/></svg>www.kiteloftdev.example</li>
    </ul>

    <div class="brand"><span>KITE</span><span class="brand__dot"></span><span>LOFT</span></div>

    <div class="holder">
      <p class="holder__name">Corwin T. Aldous</p>
      <p class="holder__role">Open Source Web Tinkerer</p>
    </div>
  </div>
</body>
</html>
```